Automotive component supplier needs a business card design

We need a business card design for our company called Velran Global Components Ltd based in the UK. We are a supplier of interior and exterior components to premium car manufacturers such as Corvel Ashby, Hadley Fenn, Marquist and Tavarelli. We would like to see a modern business card design that uses the colour blue.

Target Market(s)

Premium automotive car manufacturers.

Industry/Entity Type

Automotive

Contact Information for Business Card

Company Name : Velran Global Components Limited
Address: 17 Marlow Yard, Upper Heath, Warwick, CV31 8QL, United Kingdom
Web Address : www.velrancomponents-example.co.uk

Font styles to use
Other font styles liked:
• Helvetica

Colors
3176b5
0255a3
85acd3
cfdeed
cee9f5
85cae6
34a6d7
0692cd
9bcb3c

Requirements
Must have
• Clear company logo and a mixture of blue colours.
Nice to have
• A high quality modern image.
Should not have
• Multiple colours.

```html
<!DOCTYPE html>
<html lang="en">
<head>
<meta charset="utf-8">
<title>Velran Global Components – Business Card</title>
<link rel="stylesheet" href="https://fonts.googleapis.com/css2?family=Arimo:wght@400;700&display=swap">
<style>
  :root {
    --backdrop: #2b2b2d;
    --card-white: #ffffff;
    --brand-blue: #1a8fd3;
    --brand-green: #8dc63f;
    --ink: #4a4a4a;
    --ink-soft: #6b6b6b;
  }
  * { margin: 0; padding: 0; box-sizing: border-box; }
  html, body {
    width: 1200px; height: 950px; overflow: hidden;
    background: var(--backdrop);
    font-family: "Arimo", Helvetica, Arial, sans-serif;
  }
  .card {
    position: absolute; left: 250px;
    width: 700px; height: 400px;
    border-radius: 4px;
    box-shadow: 0 10px 30px rgba(0,0,0,.45);
    overflow: hidden;
  }
  /* Front */
  .card-front { top: 50px; background: var(--card-white); }
  .front-brand {
    position: absolute; left: 44px; top: 120px;
    color: var(--brand-blue); font-weight: 700;
    font-size: 30px; letter-spacing: .5px; text-transform: uppercase;
  }
  .rule-blue {
    position: absolute; left: 44px; top: 168px;
    width: 470px; height: 3px; background: var(--brand-blue);
  }
  .rule-green {
    position: absolute; left: 514px; top: 168px;
    width: 150px; height: 3px; background: var(--brand-green);
  }
  .holder {
    position: absolute; right: 36px; top: 118px; text-align: right;
  }
  .holder-name { color: var(--brand-blue); font-size: 22px; font-weight: 700; }
  .holder-role { color: var(--brand-green); font-size: 15px; margin-top: 3px; }
  .address {
    position: absolute; right: 36px; top: 196px; text-align: right;
    color: var(--ink); font-size: 14px; line-height: 1.5;
    list-style: none;
  }
  .contacts {
    position: absolute; left: 44px; bottom: 40px;
    list-style: none; color: var(--ink); font-size: 14px; line-height: 1;
  }
  .contacts li { display: flex; align-items: center; gap: 10px; margin-top: 9px; }
  .contacts svg { width: 14px; height: 14px; fill: var(--brand-blue); flex: none; }
  /* Back */
  .card-back { top: 500px; background: var(--brand-green); }
  .back-brand {
    position: absolute; left: 60px; top: 110px;
    color: var(--card-white); font-weight: 700; text-transform: uppercase;
    font-size: 50px; line-height: 1.05; letter-spacing: 1px;
  }
  .back-web {
    position: absolute; left: 62px; bottom: 70px;
    color: var(--card-white); font-size: 15px; letter-spacing: 4px;
  }
</style>
</head>
<body>

<section class="card card-front" aria-label="Business card front">
  <div class="front-brand">Velran Global Components</div>
  <div class="rule-blue"></div>
  <div class="rule-green"></div>

  <div class="holder">
    <div class="holder-name">Darren Holt</div>
    <div class="holder-role">President</div>
  </div>

  <ul class="address">
    <li>17 Marlow Yard</li>
    <li>Upper Heath</li>
    <li>Warwick, CV31 8QL</li>
    <li>United Kingdom</li>
  </ul>

  <ul class="contacts">
    <li>
      <svg viewBox="0 0 16 16" aria-hidden="true"><path d="M3 1h3l1.5 4-2 1.3a9 9 0 0 0 4.2 4.2L11 8.5l4 1.5v3a2 2 0 0 1-2 2A12 12 0 0 1 1 3a2 2 0 0 1 2-2z"/></svg>
      555 0142 7731
    </li>
    <li>
      <svg viewBox="0 0 16 16" aria-hidden="true"><path d="M4 0h8a1 1 0 0 1 1 1v14a1 1 0 0 1-1 1H4a1 1 0 0 1-1-1V1a1 1 0 0 1 1-1zm1 2v10h6V2zm3 11a1 1 0 1 0 0 2 1 1 0 0 0 0-2z"/></svg>
      555 0198 4620
    </li>
    <li>
      <svg viewBox="0 0 16 16" aria-hidden="true"><path d="M0 3h16v10H0zm1.5 1.2v.3L8 9l6.5-4.5v-.3z"/></svg>
      darren@velrancomponents-example.co.uk
    </li>
    <li>
      <svg viewBox="0 0 16 16" aria-hidden="true"><path d="M8 0a8 8 0 1 0 0 16A8 8 0 0 0 8 0zm0 1.5c1 1.2 1.7 3.2 1.8 5.5H6.2C6.3 4.7 7 2.7 8 1.5zM6.2 9h3.6c-.1 2.3-.8 4.3-1.8 5.5-1-1.2-1.7-3.2-1.8-5.5zM1.6 7a6.5 6.5 0 0 1 3.2-4.7A11 11 0 0 0 4.2 7zm0 2h2.6a11 11 0 0 0 .6 4.7A6.5 6.5 0 0 1 1.6 9zm9.6 4.7a11 11 0 0 0 .6-4.7h2.6a6.5 6.5 0 0 1-3.2 4.7zM11.8 7a11 11 0 0 0-.6-4.7A6.5 6.5 0 0 1 14.4 7z"/></svg>
      www.velrancomponents-example.co.uk
    </li>
  </ul>
</section>

<section class="card card-back" aria-label="Business card back">
  <div class="back-brand">Velran<br>Global Components</div>
  <div class="back-web">www.velrancomponents-example.co.uk</div>
</section>

</body>
</html>
```